Computer Security FaceBook start-up design.

Should be in Harmony with https://www.quorvant.com We need a design for our facebook profile for our company Quorvant. We work at computer security consulting services and licensing offering a high technological MothGuard. A Framework That Allows any security based company to analyze / monitorize / etc. really any application with high performance and stealth based on hypervisor technologies. Our main color is RED, as you will see in our logo. The design Should our deep expertise transmit / skills on security. We would like to have MothGuard Also Represented as Lynx With an Anything That Could That remark is Iberian Lynx (if possible). Any questions are welcome :)

Industry/Entity Type

Computer Security

Requirements
Must have
• Should be in armony With https://www.quorvant.com

```html
<!DOCTYPE html>
<html lang="en">
<head>
<meta charset="utf-8">
<title>Quorvant – Cover</title>
<link rel="stylesheet" href="https://fonts.googleapis.com/css2?family=Montserrat:wght@400;500;600&display=swap">
<style>
  :root {
    --red: #e8434b;
    --red-deep: #c93a41;
    --navy: #35475c;
    --navy-deep: #2b3b4e;
    --panel: #e6ebf0;
    --ink: #4a4f57;
    --white: #ffffff;
    --page: #f2f3f5;
  }
  * { margin: 0; padding: 0; box-sizing: border-box; }
  html, body {
    width: 1200px; height: 648px; overflow: hidden;
    background: var(--page);
    font-family: "Montserrat", sans-serif;
  }
  .cover {
    position: absolute; left: 40px; top: 112px;
    width: 1120px; height: 424px;
    background: var(--white);
    overflow: hidden;
  }
  .hero-visual {
    position: absolute; left: 0; top: 0; width: 760px; height: 424px;
    background: radial-gradient(ellipse at 35% 45%, #ffffff 0%, #e9ebee 55%, #cfd3d8 100%);
  }
  .backdrop { position: absolute; inset: 0; }
  .stripe { position: absolute; }
  .stripe--red-top { left: 894px; top: 0; width: 92px; height: 170px; background: var(--red-deep); }
  .stripe--navy-mid { left: 747px; top: 130px; width: 48px; height: 294px; background: var(--navy-deep); }
  .stripe--red-low { left: 594px; top: 250px; width: 92px; height: 174px; background: var(--red-deep); }
  .stripe--navy-low { left: 476px; top: 380px; width: 59px; height: 44px; background: var(--navy-deep); }

  .contact {
    position: absolute; right: 410px; top: 30px; text-align: right;
    color: var(--ink); font-size: 15px; line-height: 22px;
  }
  .contact__title { color: var(--red); font-size: 22px; font-weight: 500; letter-spacing: .5px; margin-bottom: 4px; }
  .contact__line { display: flex; justify-content: flex-end; align-items: center; gap: 8px; }
  .contact__line svg { width: 12px; height: 12px; fill: var(--ink); }

  .feature {
    position: absolute; display: flex; align-items: center; gap: 14px;
    padding: 0 16px; color: var(--white);
  }
  .feature--navy { background: var(--navy); }
  .feature--red { background: var(--red); }
  .feature__icon { width: 48px; height: 48px; flex: none; }
  .feature__title { font-size: 22px; font-weight: 500; letter-spacing: .5px; line-height: 26px; }
  .feature__text { font-size: 14.5px; line-height: 18px; margin-top: 2px; }
  .feature--memory { left: 747px; top: 43px; width: 360px; height: 90px; }
  .feature--anticheat { left: 594px; top: 167px; width: 368px; height: 87px; }
  .feature--intel { left: 448px; top: 294px; width: 388px; height: 89px; }

  .cta { position: absolute; left: 858px; top: 272px; width: 250px; color: var(--ink); }
  .cta__title { color: var(--red); font-size: 22px; font-weight: 500; letter-spacing: .5px; margin-bottom: 8px; }
  .cta__text { font-size: 14.5px; line-height: 19px; }
  .cta__arrow { position: absolute; left: 1018px; top: 398px; width: 26px; height: 14px; }
</style>
</head>
<body>
<main class="cover">
  <div class="hero-visual" role="img" aria-label="Silver humanoid robot head with glowing eyes over a faint grey network of connected dots"></div>

  <svg class="backdrop" width="1120" height="424" viewBox="0 0 1120 424" aria-hidden="true">
    <polygon fill="var(--panel)" points="760,0 1120,0 1120,424 430,424 430,270 575,270 575,150 735,150 735,20 760,20"/>
  </svg>

  <div class="stripe stripe--red-top"></div>
  <div class="stripe stripe--navy-mid"></div>
  <div class="stripe stripe--red-low"></div>
  <div class="stripe stripe--navy-low"></div>

  <section class="contact">
    <h2 class="contact__title">CONTACT INFO</h2>
    <p class="contact__line">+34 911 527 304
      <svg viewBox="0 0 24 24"><path d="M6.6 10.8a15.1 15.1 0 0 0 6.6 6.6l2.2-2.2a1 1 0 0 1 1-.25 11.4 11.4 0 0 0 3.6.57 1 1 0 0 1 1 1V20a1 1 0 0 1-1 1A17 17 0 0 1 3 4a1 1 0 0 1 1-1h3.5a1 1 0 0 1 1 1c0 1.25.2 2.45.57 3.57a1 1 0 0 1-.25 1z"/></svg>
    </p>
    <p class="contact__line">info@quorvant.com
      <svg viewBox="0 0 24 24"><path d="M2 5h20v2l-10 6L2 7z M2 9l10 6 10-6v10H2z"/></svg>
    </p>
  </section>

  <article class="feature feature--navy feature--memory">
    <svg class="feature__icon" viewBox="0 0 48 48" fill="none" stroke="#fff" stroke-width="2.4" stroke-linejoin="round" stroke-linecap="round">
      <path d="M24 5 L40 11 V23 C40 33 33 40 24 43 C15 40 8 33 8 23 V11 Z"/>
      <path d="M17 24 L22 29 L31 19"/>
    </svg>
    <div>
      <h3 class="feature__title">MEMORY GUARD</h3>
      <p class="feature__text">Virtualization based dynamic code and data interception toolkit</p>
    </div>
  </article>

  <article class="feature feature--red feature--anticheat">
    <svg class="feature__icon" viewBox="0 0 48 48" fill="none" stroke="#fff" stroke-width="2.4" stroke-linecap="round">
      <circle cx="24" cy="24" r="16"/>
      <path d="M12.7 12.7 L35.3 35.3"/>
    </svg>
    <div>
      <h3 class="feature__title">ANTI-CHEAT</h3>
      <p class="feature__text">Smash advanced cheaters leveraging deep learning technologies</p>
    </div>
  </article>

  <article class="feature feature--navy feature--intel">
    <svg class="feature__icon" viewBox="0 0 48 48" fill="#fff" stroke="#fff" stroke-width="2">
      <circle cx="24" cy="24" r="6"/>
      <line x1="24" y1="24" x2="24" y2="6"/><circle cx="24" cy="6" r="3"/>
      <line x1="24" y1="24" x2="40" y2="15"/><circle cx="40" cy="15" r="3"/>
      <line x1="24" y1="24" x2="40" y2="34"/><circle cx="40" cy="34" r="3"/>
      <line x1="24" y1="24" x2="24" y2="42"/><circle cx="24" cy="42" r="3"/>
      <line x1="24" y1="24" x2="8" y2="34"/><circle cx="8" cy="34" r="3"/>
      <line x1="24" y1="24" x2="8" y2="15"/><circle cx="8" cy="15" r="3"/>
    </svg>
    <div>
      <h3 class="feature__title">THREAT INTELLIGENCE</h3>
      <p class="feature__text">Seasoned cybersecurity experts to analyze relevant threat intelligence</p>
    </div>
  </article>

  <section class="cta">
    <h2 class="cta__title">WORK WITH US ?</h2>
    <p class="cta__text">Build your solution over the solid foundation provided by our top class development kit.</p>
  </section>
  <svg class="cta__arrow" viewBox="0 0 26 14" aria-hidden="true"><polygon points="0,0 26,0 13,14" fill="var(--red)"/></svg>
</main>
</body>
</html>
```